Communication and Marketing agency needs a new presentation card

We are a group of communication and marketing agencies specialized in companies that are in the logistics and industrial sector. The head agency is TELVANO Grupo and the group consists of 4 agencies: TELVANO Media, TELVANO Digital, TELVANO Research and DifundeEnPantalla. We hace 4 offices in Spain (Madrid, Barcelona, Valencia and Murcia). We are looking for a clean and attractive design that transmits our experience, brand presence in the market and knowledge to those who receive the card.It has to maintain the colors of the logo that is attached.
Target Market(s)
logistics and industrial sector
Marketing department
Contact Information for Business Card
Clean and attractive design

```html
<!DOCTYPE html>
<html lang="en">
<head>
<meta charset="utf-8">
<title>TELVANO Business Card</title>
<link href="https://fonts.googleapis.com/css2?family=Oswald:wght@400;600&family=Lato:wght@400&display=swap" rel="stylesheet">
<style>
  :root {
    --bg-red: #a51e22;
    --brand-red: #b31f2b;
    --brand-grey: #555557;
    --band-grey: #4f4d4b;
    --card-white: #f9f9f9;
    --text-white: #ffffff;
  }
  html, body {
    margin: 0;
    padding: 0;
    width: 1200px;
    height: 1200px;
    overflow: hidden;
    background: var(--bg-red);
  }
  .canvas {
    position: relative;
    width: 1200px;
    height: 1200px;
  }
  .card {
    position: absolute;
    left: 224px;
    width: 814px;
    height: 466px;
    background: var(--card-white);
  }
  .card--front { top: 76px; border-radius: 24px; }
  .card--back { top: 658px; }

  .wordmark {
    position: absolute;
    text-align: right;
    font-family: "Oswald", sans-serif;
    font-weight: 400;
    line-height: 1;
  }
  .wordmark__name { display: block; font-size: 96px; letter-spacing: 4px; }
  .wordmark__sub { display: block; font-size: 52px; margin-top: 2px; }

  .card--front .wordmark { right: 152px; top: 148px; color: var(--brand-grey); }
  .card--back .wordmark { right: 187px; top: 58px; color: var(--brand-red); }

  .name-band {
    position: absolute;
    left: 0;
    top: 302px;
    width: 392px;
    height: 84px;
    background: var(--band-grey);
    color: var(--text-white);
    text-align: right;
    box-sizing: border-box;
    padding-right: 20px;
  }
  .name-band__name {
    font-family: "Oswald", sans-serif;
    font-weight: 600;
    font-size: 40px;
    line-height: 1;
    margin-top: 8px;
    letter-spacing: 1px;
  }
  .name-band__credentials {
    font-family: "Lato", sans-serif;
    font-size: 19px;
    margin-top: 4px;
  }

  .contact-band {
    position: absolute;
    left: 407px;
    top: 302px;
    width: 407px;
    height: 84px;
    background: var(--brand-red);
    color: var(--text-white);
    font-family: "Lato", sans-serif;
    font-size: 20px;
    box-sizing: border-box;
    padding: 3px 0 0 30px;
  }
  .contact-band__notch {
    position: absolute;
    left: -15px;
    top: 26px;
    width: 0;
    height: 0;
    border-top: 16px solid transparent;
    border-bottom: 16px solid transparent;
    border-right: 15px solid var(--brand-red);
  }
  .contact-item {
    display: flex;
    align-items: center;
    gap: 8px;
    height: 27px;
  }
  .contact-item svg { width: 14px; height: 14px; flex: none; }
</style>
</head>
<body>
<div class="canvas">
  <section class="card card--front">
    <div class="wordmark">
      <span class="wordmark__name">TELVANO</span>
      <span class="wordmark__sub">Digital</span>
    </div>
  </section>

  <section class="card card--back">
    <div class="wordmark">
      <span class="wordmark__name">TELVANO</span>
      <span class="wordmark__sub">Grupo</span>
    </div>

    <div class="name-band">
      <div class="name-band__name">LARS VENN</div>
      <div class="name-band__credentials">BSc(kin), MPT, CAFCI, IMS</div>
    </div>

    <div class="contact-band">
      <span class="contact-band__notch"></span>
      <div class="contact-item">
        <svg viewBox="0 0 16 16" aria-hidden="true"><path fill="#fff" d="M3.5 1l2.5 3-1.5 1.8c.8 1.9 2.3 3.4 4.2 4.2L10.5 8.5l3 2.5-1.3 2.7c-.3.5-.9.8-1.5.6C6 13 3 10 1.7 5.3c-.2-.6.1-1.2.6-1.5z"/></svg>
        <span>555-214-0398</span>
      </div>
      <div class="contact-item">
        <svg viewBox="0 0 16 16" aria-hidden="true"><rect x="1" y="3" width="14" height="10" fill="#fff"/><path d="M1 3l7 6 7-6M1 13l5-5M15 13l-5-5" stroke="#b31f2b" stroke-width="1.2" fill="none"/></svg>
        <span>VennPhysio@mailbox.com</span>
      </div>
      <div class="contact-item">
        <svg viewBox="0 0 16 16" aria-hidden="true"><g fill="none" stroke="#fff" stroke-width="1.2"><circle cx="8" cy="8" r="6.5"/><ellipse cx="8" cy="8" rx="3" ry="6.5"/><path d="M1.5 8h13M2.5 4.8h11M2.5 11.2h11"/></g></svg>
        <span>www.VennPhysio.ca</span>
      </div>
    </div>
  </section>
</div>
</body>
</html>
```